Business Card for a Dental Office

The design should communicate integrity, quality and reliability. We also want the card look elegant, simple, but still stand out, different from the traditional-dental-office business card.

Industry/Entity Type

Business

```html
<!DOCTYPE html>
<html lang="en">
<head>
<meta charset="utf-8">
<title>Harwell Dental Centre – Business Card</title>
<link rel="stylesheet" href="https://fonts.googleapis.com/css2?family=Oswald:wght@500;700&family=Open+Sans:wght@400;600&display=swap">
<style>
  :root {
    --card-black: #0b0b0b;
    --card-sheen: #262626;
    --gold: #c9b52c;
    --white: #f4f4f4;
    --grey: #8a8a8a;
    --ink: #1b1b14;
    --page: #d9d6cf;
  }
  html, body {
    margin: 0;
    width: 1200px;
    height: 1022px;
    overflow: hidden;
    background: var(--page);
  }
  .card {
    position: absolute;
    left: 100px;
    top: 225px;
    width: 1000px;
    height: 572px;
    border-radius: 22px;
    overflow: hidden;
    background: radial-gradient(ellipse at 55% 35%, var(--card-sheen) 0%, var(--card-black) 60%);
    box-shadow: 0 18px 40px rgba(0,0,0,.35);
  }
  .card-shapes { position: absolute; inset: 0; }
  .clinic-name {
    position: absolute;
    left: 44px;
    top: 34px;
    margin: 0;
    font-family: "Oswald", sans-serif;
    font-weight: 700;
    font-size: 70px;
    line-height: 1.1;
    letter-spacing: 1px;
    color: var(--white);
    text-transform: uppercase;
    white-space: nowrap;
  }
  .tagline {
    position: absolute;
    left: 46px;
    top: 122px;
    margin: 0;
    font-family: "Oswald", sans-serif;
    font-weight: 500;
    font-size: 34px;
    letter-spacing: 2px;
    color: var(--gold);
    text-transform: uppercase;
    white-space: nowrap;
  }
  .person {
    position: absolute;
    left: 244px;
    top: 304px;
  }
  .person-name {
    margin: 0;
    font-family: "Oswald", sans-serif;
    font-weight: 700;
    font-size: 30px;
    line-height: 1.1;
    color: var(--gold);
    text-transform: uppercase;
  }
  .person-role {
    margin: 4px 0 0;
    font-family: "Open Sans", sans-serif;
    font-size: 15px;
    letter-spacing: 1px;
    color: var(--grey);
    text-transform: uppercase;
  }
  .contact {
    position: absolute;
    left: 250px;
    top: 450px;
    margin: 0;
    padding: 0;
    list-style: none;
    font-family: "Open Sans", sans-serif;
    font-size: 19px;
    color: var(--ink);
  }
  .contact li {
    display: flex;
    align-items: center;
    gap: 12px;
    height: 32px;
  }
  .contact svg { width: 16px; height: 16px; }
  .brand-mark {
    position: absolute;
    left: 870px;
    top: 142px;
    width: 130px;
    height: 128px;
    display: flex;
    align-items: center;
    justify-content: center;
    font-family: "Oswald", sans-serif;
    font-weight: 700;
    font-size: 22px;
    letter-spacing: 1px;
    color: var(--ink);
    text-transform: uppercase;
  }
</style>
</head>
<body>
  <article class="card">
    <svg class="card-shapes" viewBox="0 0 1000 572" aria-hidden="true">
      <polygon fill="var(--white)" points="0,418 215,418 238,396 846,396 846,410 246,410 224,432 0,432"/>
      <polygon fill="var(--gold)" points="0,440 228,440 250,418 1000,418 1000,572 0,572"/>
      <rect x="202" y="360" width="32" height="30" fill="var(--gold)"/>
      <polyline fill="none" stroke="var(--white)" stroke-width="12" stroke-linejoin="miter" points="840,410 840,172 902,110 1010,110"/>
      <rect x="870" y="142" width="130" height="128" fill="var(--gold)"/>
    </svg>

    <h1 class="clinic-name">Harwell Dental Centre</h1>
    <p class="tagline">Your smile is your gift to others</p>

    <div class="person">
      <p class="person-name">Alan Reyes</p>
      <p class="person-role">Director</p>
    </div>

    <div class="brand-mark">Harwell</div>

    <ul class="contact">
      <li>
        <svg viewBox="0 0 16 16"><path fill="var(--ink)" d="M3 1l3 3-2 2c1 2 3 4 5 5l2-2 3 3-2 3C6 15 1 10 1 3z"/></svg>
        +330 5550-0142
      </li>
      <li>
        <svg viewBox="0 0 16 16"><rect x="1" y="3" width="14" height="10" fill="none" stroke="var(--ink)" stroke-width="1.6"/><path d="M1 3l7 6 7-6" fill="none" stroke="var(--ink)" stroke-width="1.6"/></svg>
        info@harwelldentalcentre.com
      </li>
      <li>
        <svg viewBox="0 0 16 16"><circle cx="8" cy="8" r="6.5" fill="none" stroke="var(--ink)" stroke-width="1.5"/><ellipse cx="8" cy="8" rx="3" ry="6.5" fill="none" stroke="var(--ink)" stroke-width="1.2"/><path d="M1.5 8h13" stroke="var(--ink)" stroke-width="1.2"/></svg>
        www.harwelldentalcentre.com
      </li>
    </ul>
  </article>
</body>
</html>
```